Greeting Card Design - Bright Hearts Open Pages

Hi there

Thank you for taking the time to read about this project.

The project is for a range of greeting cards for the gay and lesbian community. The brand is called "Bright Hearts Open Pages".

In this project I require four designs in total (designs for homosexual couples, two for men and two for women). The designs need to reflect the general concept of being in love.

I am looking for variety (fun and funky, as well as modern and classy - please design to your tastes and I will give feedback).

I will work with each designer closely and provide the words for the cards as the designs are developed.

Thank you for considering this project.
Updates

I'm currently having issues with the craft huddle website and it won't let me upload files to show the logo. I will do so as soon as the website allows me. Thanks

Target Market(s)

Gay and lesbian community.

Industry/Entity Type

Community

Requirements
Must have
• I am looking for variety in the range. I would like designs that are modern and classy range; and also designs that are fun and funky.
Nice to have
• Hand drawings are good for the fun range, so is colour.
The classy range can be symbolic (e.g. holding hands) or black and whites.
Should not have
• Please do not use rainbows or rainbow coloured font.

```html
<!DOCTYPE html>
<html lang="en">
<head>
<meta charset="utf-8">
<title>Bright Hearts Open Pages – My love card</title>
<link rel="stylesheet" href="https://fonts.googleapis.com/css2?family=Nothing+You+Could+Do&display=swap">
<style>
  :root {
    --paper: #ffffff;
    --ink: #2b2b2b;
    --rule: #6d6d6d;
    --brand-red: #be1e2d;
    --frame-taupe: #928279;
    --photo-dark: #2f2f2f;
    --photo-mid: #7a7a7a;
    --photo-light: #d9d9d9;
    --hand: "Nothing You Could Do", cursive;
  }
  html, body {
    margin: 0;
    padding: 0;
    width: 813px;
    height: 1200px;
    overflow: hidden;
    background: var(--paper);
  }
  .canvas {
    position: relative;
    width: 813px;
    height: 1200px;
  }

  /* Outside spread */
  .outside {
    position: absolute;
    left: 23px;
    top: 18px;
    width: 766px;
    height: 557px;
    border: 1px solid var(--rule);
    box-sizing: border-box;
    background: var(--paper);
  }
  .back-cover {
    position: absolute;
    left: 0;
    top: 0;
    width: 384px;
    height: 100%;
  }
  .hang-string {
    position: absolute;
    left: 0;
    top: 0;
  }
  .hang-tag {
    position: absolute;
    left: 130px;
    top: 60px;
    width: 124px;
    height: 124px;
    border-radius: 50%;
    background: var(--brand-red);
    display: flex;
    align-items: center;
    justify-content: center;
    text-align: center;
  }
  .hang-tag__hole {
    position: absolute;
    left: 59px;
    top: 6px;
    width: 6px;
    height: 6px;
    border-radius: 50%;
    background: var(--paper);
  }
  .hang-tag__name {
    font-family: var(--hand);
    color: var(--paper);
    font-size: 17px;
    line-height: 1.1;
    width: 90px;
    margin-top: 12px;
  }
  .front-cover {
    position: absolute;
    right: 0;
    top: 0;
    width: 382px;
    height: 100%;
    overflow: hidden;
  }
  .cover-photo {
    position: absolute;
    inset: 0;
    background:
      linear-gradient(160deg, var(--photo-mid) 0%, var(--photo-light) 18%, var(--photo-dark) 35%, var(--photo-dark) 60%, var(--photo-light) 78%, var(--photo-mid) 100%);
  }
  .title-band {
    position: absolute;
    left: 0;
    top: 259px;
    width: 244px;
    height: 73px;
    background: var(--brand-red);
    display: flex;
    align-items: center;
    justify-content: center;
  }
  .title-band__text {
    font-family: var(--hand);
    color: var(--paper);
    font-size: 50px;
    line-height: 1;
    margin: 0;
    font-weight: 400;
  }

  /* Inside spread */
  .inside {
    position: absolute;
    left: 23px;
    top: 628px;
    width: 766px;
    height: 557px;
    box-sizing: border-box;
    border: 16px solid var(--frame-taupe);
    background: var(--paper);
  }
  .inside__fold {
    position: absolute;
    left: 368px;
    top: -16px;
    height: calc(100% + 32px);
    border-left: 1px dashed var(--rule);
  }
  .inside__message {
    position: absolute;
    left: 384px;
    top: 162px;
    width: 350px;
    margin: 0;
    text-align: center;
    font-family: var(--hand);
    color: var(--ink);
    font-size: 21px;
    line-height: 48px;
  }
</style>
</head>
<body>
<div class="canvas">
  <section class="outside">
    <div class="back-cover">
      <svg class="hang-string" width="384" height="90" viewBox="0 0 384 90" aria-hidden="true">
        <path d="M247 0 L211 66" stroke="#8a8a8a" stroke-width="1.2" fill="none"/>
        <path d="M198 68 Q218 56 232 52" stroke="#8a8a8a" stroke-width="1.2" fill="none"/>
      </svg>
      <div class="hang-tag">
        <span class="hang-tag__hole"></span>
        <span class="hang-tag__name">Bright Hearts Open Pages</span>
      </div>
    </div>
    <div class="front-cover">
      <div class="cover-photo" role="img" aria-label="Black and white posterised photograph of a couple embracing, hands resting on a dark ruffled dress"></div>
      <div class="title-band">
        <h1 class="title-band__text">My love...</h1>
      </div>
    </div>
  </section>

  <section class="inside">
    <div class="inside__fold"></div>
    <p class="inside__message">Everything is better<br>with you by my side.<br>I love you</p>
  </section>
</div>
</body>
</html>
```